you will use Ai to Copy the website Brivanta.com to come up with the basic frame work and it will give you the understanding of how I would like Kelbrava.com to be like. Kelbrava.com is a peer to peer rv rental site very similar to both of the other rv rental sites the difference is that are commission based 20% and above per rental and we will be one flat monthly rate and they keep all the earnings. Below is photo that will help you with the color scheme and the look and feel of the design

1 page

```html
<!DOCTYPE html>
<html lang="en">
<head>
<meta charset="utf-8">
<title>Kelbrava.com — Peer-to-peer RV rentals</title>
<link href="https://fonts.googleapis.com/css2?family=Inter:wght@400;500;600;700;800&family=Inter+Tight:wght@700;800&display=swap" rel="stylesheet">
<style>
:root{
  --green:#5a9e3e;
  --navy:#12233a;
  --amber:#f6b443;
  --ink:#13202f;
  --muted:#5b6472;
  --line:#e4e7ec;
  --soft:#f5f7f9;
  --white:#ffffff;
}
*{box-sizing:border-box;margin:0;padding:0}
html,body{width:1140px;height:1200px;overflow:hidden}
body{font-family:"Inter",sans-serif;color:var(--ink);background:var(--white);position:relative}
.hero{position:absolute;left:0;top:0;width:1140px;height:489px;
  background:linear-gradient(180deg,rgba(40,30,30,.25),rgba(20,20,20,.35)),
  linear-gradient(100deg,#8a4a32 0%,#a8623f 30%,#7b5a48 55%,#9c6b54 75%,#6d5b4c 100%);}
.hero-photo{position:absolute;inset:0;background:linear-gradient(180deg,transparent 55%,rgba(105,100,85,.75) 75%,rgba(70,70,66,.9) 100%)}
.nav{position:absolute;left:146px;right:146px;top:12px;height:34px;display:flex;align-items:center;color:var(--white)}
.logo{font-weight:700;font-size:15px;letter-spacing:-.3px}
.nav-links{position:absolute;left:225px;display:flex;align-items:center;gap:21px;font-size:11px;font-weight:500}
.pill-outline{border:1px solid rgba(255,255,255,.55);border-radius:20px;padding:5px 13px;background:rgba(255,255,255,.12)}
.nav-right{position:absolute;right:0;display:flex;align-items:center;gap:14px;font-size:11px;font-weight:500}
.signup{border:1.5px solid rgba(255,255,255,.8);border-radius:20px;padding:9px 17px;font-weight:600}
.eyebrow{position:absolute;left:146px;top:143px;border:1px solid rgba(246,180,67,.7);border-radius:14px;padding:5px 10px;
  font-size:9.5px;font-weight:700;letter-spacing:1.6px;color:var(--amber);background:rgba(246,180,67,.12)}
.headline{position:absolute;left:146px;top:176px;font-family:"Inter Tight",sans-serif;font-weight:800;font-size:49px;line-height:50px;letter-spacing:-2.2px;color:var(--white)}
.lede{position:absolute;left:146px;top:287px;width:380px;font-size:14.5px;line-height:22px;color:rgba(255,255,255,.9)}
.search{position:absolute;left:146px;top:361px;width:667px;height:80px;background:var(--white);border-radius:18px;overflow:hidden}
.tabs{display:flex;height:32px;border-bottom:1px solid var(--line);font-size:10px;font-weight:500;padding-left:17px;gap:36px;align-items:center;color:var(--muted)}
.tab-active{color:var(--ink);height:32px;display:flex;align-items:center;border-bottom:2px solid var(--green);padding:0 0;font-weight:600}
.fields{display:flex;height:48px}
.field{width:142px;padding:11px 15px;border-right:1px solid var(--line);margin:5px 0}
.field:nth-child(4){border-right:none}
.field-label{font-size:7.5px;font-weight:700;letter-spacing:.9px}
.field-value{font-size:11px;color:#b3b8c0;margin-top:5px}
.field-value.filled{color:var(--muted)}
.search-btn{margin-left:auto;width:98px;background:var(--green);color:var(--white);display:flex;align-items:center;justify-content:center;gap:6px;font-size:11px;font-weight:600}
.band{position:absolute;left:0;top:489px;width:1140px;height:104px;background:var(--navy);display:flex;padding-left:168px}
.perk{width:212px;display:flex;align-items:center;gap:13px;position:relative}
.perk+ .perk::before{content:"";position:absolute;left:-11px;top:37px;height:30px;width:1px;background:rgba(255,255,255,.15)}
.perk-icon{font-size:17px;width:20px}
.perk h3{font-size:11px;font-weight:700;color:var(--white)}
.perk p{font-size:9.5px;line-height:15px;color:rgba(255,255,255,.7);margin-top:3px;width:130px}
.promos{position:absolute;left:146px;top:629px;display:flex;gap:18px}
.promo{width:415px;height:237px;border-radius:16px;position:relative;overflow:hidden;padding:47px 24px 0}
.promo-delivery{background:linear-gradient(120deg,#b5621c 0%,#6a3412 35%,#4f7b8a 55%,#2b2620 85%)}
.promo-pickup{background:linear-gradient(120deg,#c9c2a6 0%,#c8a56e 45%,#b58a4f 75%,#9d7345 100%)}
.promo .tag{display:inline-block;font-size:8px;font-weight:700;letter-spacing:1.3px;padding:4px 9px;border-radius:11px}
.promo-delivery .tag{background:rgba(0,0,0,.35);border:1px solid rgba(255,255,255,.3);color:#f2e6da}
.promo-pickup .tag{background:rgba(246,180,67,.25);border:1px solid rgba(246,180,67,.5);color:var(--amber)}
.promo h2{font-family:"Inter Tight",sans-serif;font-weight:800;font-size:23px;line-height:26px;letter-spacing:-.8px;color:var(--white);margin-top:8px}
.promo p{font-size:10px;line-height:17px;color:rgba(255,255,255,.9);margin-top:10px;width:270px}
.promo .cta{display:inline-block;margin-top:15px;padding:9px 17px;border-radius:20px;font-size:11px;font-weight:600}
.promo-delivery .cta{background:var(--white);color:var(--ink)}
.promo-pickup .cta{background:var(--amber);color:var(--ink)}
.listings{position:absolute;left:0;top:914px;width:1140px;height:286px;background:var(--soft);padding:60px 146px 0}
.listings h2{font-family:"Inter Tight",sans-serif;font-size:29px;font-weight:800;letter-spacing:-.8px}
.listings .sub{font-size:12px;color:var(--muted);margin-top:6px}
.chips{display:flex;gap:7px;margin-top:25px}
.chip{height:25px;padding:0 14px;border:1px solid var(--line);border-radius:14px;background:var(--white);display:flex;align-items:center;gap:5px;font-size:10.5px;color:#3c4552}
.chip.active{background:var(--navy);color:var(--white);border-color:var(--navy)}
.cards{display:flex;gap:17px;margin-top:27px}
.card{width:272px;height:120px;border-radius:12px 12px 0 0;position:relative}
.c1{background:linear-gradient(180deg,#6a90b8 0%,#d7dde3 40%,#52677a 70%,#3e6a40 100%)}
.c2{background:linear-gradient(135deg,#a9e3d6 0%,#a5ddd1 60%,#e3d64a 100%)}
.c3{background:radial-gradient(circle at 70% 40%,#6a6a66 0%,#1a1a1a 40%,#050505 100%)}
.badge{position:absolute;left:8px;top:8px;background:var(--white);border-radius:10px;padding:4px 7px;font-size:8px;font-weight:600;display:flex;gap:4px;align-items:center}
.badge.new{background:var(--amber)}
.fav{position:absolute;right:8px;top:8px;width:22px;height:22px;border-radius:50%;background:rgba(255,255,255,.9);display:flex;align-items:center;justify-content:center}
</style>
</head>
<body>
<section class="hero" role="img" aria-label="Photo of a yellow camper van driving a desert road between red rock formations">
  <div class="hero-photo"></div>
</section>

<header class="nav">
  <div class="logo">Kelbrava.com</div>
  <nav class="nav-links">
    <span>RV Rentals</span><span>Campgrounds</span><span>How It Works</span><span class="pill-outline">Become a Host</span>
  </nav>
  <div class="nav-right"><span>Log in</span><span class="signup">Sign up free</span></div>
</header>

<div class="eyebrow">PEER-TO-PEER · NO COMMISSION</div>
<h1 class="headline">Your next adventure<br>starts on the open road</h1>
<p class="lede">Browse thousands of owner-listed RVs available for delivery or pickup. Hosts keep every dollar they earn.</p>

<form class="search">
  <div class="tabs"><span class="tab-active">Find an RV</span><span>Get it delivered</span></div>
  <div class="fields">
    <div class="field"><div class="field-label">LOCATION</div><div class="field-value filled">kky</div></div>
    <div class="field"><div class="field-label">DATES</div><div class="field-value">Add dates</div></div>
    <div class="field"><div class="field-label">GUESTS</div><div class="field-value">2 guests</div></div>
    <div class="field"><div class="field-label">RV TYPE</div><div class="field-value">All types</div></div>
    <div class="search-btn">
      <svg width="12" height="12" viewBox="0 0 24 24" fill="none" stroke="#fff" stroke-width="2.6"><circle cx="10.5" cy="10.5" r="7"/><path d="M16 16l5 5"/></svg>
      Search
    </div>
  </div>
</form>

<section class="band">
  <div class="perk"><span class="perk-icon">💰</span><div><h3>Zero commission</h3><p>Hosts keep 100% of every rental</p></div></div>
  <div class="perk"><span class="perk-icon">📅</span><div><h3>One flat monthly fee</h3><p>No surprises, no percentage cuts</p></div></div>
  <div class="perk"><span class="perk-icon">🤝</span><div><h3>True peer-to-peer</h3><p>Real owners, real RVs, real adventures</p></div></div>
  <div class="perk"><span class="perk-icon">🛡️</span><div><h3>Protected bookings</h3><p>Verified hosts, secure payments</p></div></div>
</section>

<section class="promos">
  <article class="promo promo-delivery" role="img" aria-label="View from inside a tent opening onto a pine forest">
    <span class="tag">DELIVERY</span>
    <h2>Skip the driving.<br>Just enjoy the stay.</h2>
    <p>Have an RV delivered and set up right at your site. No driving, no setup, just relaxation.</p>
    <span class="cta">Explore delivery</span>
  </article>
  <article class="promo promo-pickup" role="img" aria-label="Vintage pop-top camper van parked by a lake at sunset">
    <span class="tag">PICK UP &amp; GO</span>
    <h2>Hit the road<br>on your terms.</h2>
    <p>Find owner-listed RVs near you, grab the keys, and go. No middleman mark-up.</p>
    <span class="cta">Browse nearby RVs</span>
  </article>
</section>

<section class="listings">
  <h2>Top-rated RVs in your area</h2>
  <p class="sub">Every listing is owner-managed. Every dollar goes back to the host.</p>
  <div class="chips">
    <span class="chip active">🔥 Popular</span>
    <span class="chip">🚐 Camper van</span>
    <span class="chip">🏠 Class A</span>
    <span class="chip">🐾 Pet-friendly</span>
    <span class="chip">💵 Best value</span>
    <span class="chip">✨ Vintage</span>
    <span class="chip">🏕️ Small trailer</span>
  </div>
  <div class="cards">
    <div class="card c1" role="img" aria-label="Listing photo of snowy mountain peaks above a turquoise lake">
      <span class="badge">⭐ Highly rated</span>
      <span class="fav"><svg width="11" height="11" viewBox="0 0 24 24" fill="none" stroke="#333" stroke-width="2"><path d="M12 21s-8-5-8-11a4.5 4.5 0 0 1 8-3 4.5 4.5 0 0 1 8 3c0 6-8 11-8 11z"/></svg></span>
    </div>
    <div class="card c2" role="img" aria-label="Listing photo of a gloved hand holding a cleaning spray bottle">
      <span class="badge">⭐ Highly rated</span>
      <span class="fav"><svg width="11" height="11" viewBox="0 0 24 24" fill="none" stroke="#333" stroke-width="2"><path d="M12 21s-8-5-8-11a4.5 4.5 0 0 1 8-3 4.5 4.5 0 0 1 8 3c0 6-8 11-8 11z"/></svg></span>
    </div>
    <div class="card c3" role="img" aria-label="Listing photo of a bird of prey against a dark background">
      <span class="badge new">🆕 New listing</span>
      <span class="fav"><svg width="11" height="11" viewBox="0 0 24 24" fill="none" stroke="#333" stroke-width="2"><path d="M12 21s-8-5-8-11a4.5 4.5 0 0 1 8-3 4.5 4.5 0 0 1 8 3c0 6-8 11-8 11z"/></svg></span>
    </div>
  </div>
</section>
</body>
</html>
```